R. Talmont Realty, Inc business card (2 sided), letterhead (1 sided) & #10 envelope (1 sided)

business card of standard size utilizing the attached logo. Side one with logo, Owen Talmont (my name), President / Broker (title), 805-317-2684 (phone), www.rtalmontrealty.example (website), 1726 Harlow Avenue, Suite 4052 San Luis Obiso, CA 93628 (business address) owen.rtalmontrealty@mailbox.example (e-mail address),
Side two - Log

Letterhead and #10 envelope in the same theme
Updates

Project Deadline Extended
Reason: I think a 2 day deadline may be a bit ambitious on my part. I have extended the deadline to 4 days. Thanks!

Industry/Entity Type

Business

```html
<!DOCTYPE html>
<html lang="en">
<head>
<meta charset="utf-8">
<title>R. Talmont Realty, Inc – Business Card</title>
<link href="https://fonts.googleapis.com/css2?family=Bitter:wght@400;700&family=Open+Sans:wght@400;600&display=swap" rel="stylesheet">
<style>
  :root {
    --backdrop: #e9e6e1;
    --card: #ffffff;
    --brand-blue: #1b6f98;
    --blue-deep: #0e3f5c;
    --blue-light: #2a8cba;
    --swoosh-grey: #3a3a3d;
    --ink: #2d2d2d;
    --rule: #2b2b2b;
  }
  * { box-sizing: border-box; margin: 0; padding: 0; }
  html, body {
    width: 1200px; height: 1183px; overflow: hidden;
    background: var(--backdrop);
  }
  .canvas { position: relative; width: 1200px; height: 1183px; }

  .card {
    position: absolute;
    width: 912px; height: 518px;
    background: var(--card);
    overflow: hidden;
  }
  .card--front { left: 45px; top: 55px; }
  .card--back { left: 242px; top: 614px; border: 2px solid var(--rule); }

  .card__wave { position: absolute; inset: 0; width: 100%; height: 100%; }

  .brand {
    position: absolute;
    display: flex; align-items: center; gap: 14px;
    font-family: 'Bitter', serif;
    font-weight: 700;
    color: var(--brand-blue);
    white-space: nowrap;
  }
  .brand__mark { background: var(--brand-blue); flex: none; }
  .card--front .brand { left: 72px; top: 110px; font-size: 40px; }
  .card--front .brand__mark { width: 26px; height: 26px; }
  .card--back .brand {
    left: 0; right: 0; top: 190px; justify-content: center; font-size: 54px;
  }
  .card--back .brand__mark { width: 34px; height: 34px; }

  .person { position: absolute; left: 70px; top: 380px; }
  .person__name {
    font-family: 'Bitter', serif; font-weight: 700;
    font-size: 34px; color: var(--brand-blue); line-height: 1.2;
  }
  .person__title {
    font-family: 'Bitter', serif; font-weight: 400;
    font-size: 26px; color: var(--ink); margin-top: 6px;
  }

  .contact {
    position: absolute; right: 30px; top: 382px;
    list-style: none;
    font-family: 'Open Sans', sans-serif; font-size: 20px;
    color: #ffffff; text-align: right;
  }
  .contact li {
    display: flex; align-items: center; justify-content: flex-end;
    gap: 8px; height: 41px;
  }
  .contact svg { width: 18px; height: 18px; flex: none; }

  .card__web {
    position: absolute; left: 0; right: 0; top: 432px;
    text-align: center;
    font-family: 'Open Sans', sans-serif; font-size: 28px;
    letter-spacing: 4px; color: var(--ink);
  }
</style>
</head>
<body>
<main class="canvas">

  <section class="card card--front" aria-label="Business card front">
    <svg class="card__wave" viewBox="0 0 912 518" preserveAspectRatio="none" aria-hidden="true">
      <defs>
        <linearGradient id="blueFill" x1="0" y1="1" x2="1" y2="0">
          <stop offset="0" stop-color="#2a8cba"/>
          <stop offset="0.55" stop-color="#16628a"/>
          <stop offset="1" stop-color="#0c3650"/>
        </linearGradient>
        <linearGradient id="greyFill" x1="0" y1="1" x2="1" y2="0">
          <stop offset="0" stop-color="#bfbfc2"/>
          <stop offset="0.4" stop-color="#55555a"/>
          <stop offset="1" stop-color="#2b2b2e"/>
        </linearGradient>
      </defs>
      <path d="M 780 0 C 900 140, 760 390, 270 518 L 912 518 L 912 0 Z" fill="url(#greyFill)"/>
      <path d="M 862 0 C 915 190, 760 410, 318 518 L 912 518 L 912 0 Z" fill="url(#blueFill)"/>
    </svg>

    <div class="brand"><span class="brand__mark"></span>R. Talmont Realty, Inc</div>

    <div class="person">
      <p class="person__name">Owen Talmont</p>
      <p class="person__title">President / Broker</p>
    </div>

    <ul class="contact">
      <li>
        <svg viewBox="0 0 24 24" aria-hidden="true"><circle cx="12" cy="12" r="11" fill="none" stroke="#fff" stroke-width="1.6"/><path d="M8.5 6.5l2 2-1.2 1.6c.8 1.7 2 2.9 3.6 3.6l1.6-1.2 2 2-1.4 1.8c-3.9-.5-7-3.6-7.5-7.5z" fill="#fff"/></svg>
        805-317-2684
      </li>
      <li>
        <svg viewBox="0 0 24 24" aria-hidden="true"><rect x="3" y="6" width="18" height="12" rx="1.5" fill="#fff"/><path d="M3.5 7l8.5 6 8.5-6" fill="none" stroke="#16628a" stroke-width="1.6"/></svg>
        owen.rtalmontrealty@mailbox.example
      </li>
      <li>
        <svg viewBox="0 0 24 24" aria-hidden="true"><circle cx="12" cy="12" r="10" fill="none" stroke="#fff" stroke-width="1.8"/><ellipse cx="12" cy="12" rx="4.2" ry="10" fill="none" stroke="#fff" stroke-width="1.5"/><path d="M2 12h20M4 7h16M4 17h16" stroke="#fff" stroke-width="1.3"/></svg>
        www.rtalmontrealty.example
      </li>
    </ul>
  </section>

  <section class="card card--back" aria-label="Business card back">
    <div class="brand"><span class="brand__mark"></span>R. Talmont Realty, Inc</div>
    <p class="card__web">www.rtalmontrealty.example</p>
  </section>

</main>
</body>
</html>
```